I have a logo and need to design the business card and stationery.
Updates

The uploaded logo image named as GREYMARSH CONSTRUCTION which is to be replaced to GREYMARSH CONTRACTS. Kindly add below details and submit the designs- Company name- Greymarsh Engineering Contracts LLP Name & Post- Kelvan Joshi (Designated Partner) Address- Block No.317, Wing C, Tulvo Trade Court, Manek Pural Road, Ruparel Industrial Estate, Goregaon(E), Mumbai - 400 063 Contact- +91 97415 60382 Email- kelvanjoshi@mailbrook.example Website- www.greymarshcontracts.example Contact for Letterhead- +91-22-28754193

Hi Tovin Rahul, We are liking your Design #28860835. We have suggested some changes which are mentioned in feedback. Kindly revert with it asap to finalize this design.

Colors

Designer to choose colors to be used in the design.

```html
<!DOCTYPE html>
<html lang="en">
<head>
<meta charset="utf-8">
<title>Greymarsh Contracts – Business Card</title>
<link href="https://fonts.googleapis.com/css2?family=Roboto:wght@400;700;900&display=swap" rel="stylesheet">
<style>
  :root {
    --backdrop: #1c1c1c;
    --card: #f4f4f4;
    --ink: #4a4a4a;
    --ink-soft: #6e6e6e;
    --rule: #8a8a8a;
  }
  * { box-sizing: border-box; margin: 0; padding: 0; }
  html, body {
    width: 1200px; height: 900px; overflow: hidden;
    background: var(--backdrop);
    font-family: "Roboto", sans-serif;
  }
  .canvas {
    width: 1200px; height: 900px;
    display: flex; align-items: center; justify-content: center;
  }
  .card {
    position: relative;
    width: 1000px; height: 571px;
    background: var(--card);
    box-shadow: 0 20px 50px rgba(0,0,0,.5);
    color: var(--ink);
  }
  .brand {
    position: absolute; right: 540px; top: 150px;
    display: flex; align-items: center; gap: 18px;
  }
  .brand-square {
    width: 26px; height: 26px; flex: none;
    background: var(--ink);
  }
  .brand-name {
    font-weight: 700; font-size: 34px; line-height: 1.2;
    letter-spacing: 2px; color: var(--ink); text-align: right;
  }
  .divider {
    position: absolute; left: 490px; top: 140px;
    width: 2px; height: 170px; background: var(--rule);
  }
  .person { position: absolute; left: 530px; top: 140px; }
  .person-name {
    font-weight: 900; font-size: 32px; letter-spacing: 1px;
    text-transform: uppercase; color: var(--ink);
  }
  .person-title {
    font-size: 24px; color: var(--ink-soft); margin-top: 4px;
  }
  .contact-list { list-style: none; margin-top: 24px; }
  .contact-list li {
    display: flex; align-items: center; gap: 10px;
    font-size: 22px; color: var(--ink); line-height: 32px;
  }
  .contact-list svg { width: 18px; height: 18px; fill: var(--ink); flex: none; }
  .address {
    position: absolute; left: 90px; bottom: 60px;
    font-style: normal;
    font-size: 21px; line-height: 30px; color: var(--ink);
  }
</style>
</head>
<body>
<main class="canvas">
  <article class="card">
    <div class="brand">
      <span class="brand-name">GREYMARSH<br>CONTRACTS</span>
      <span class="brand-square"></span>
    </div>

    <div class="divider"></div>

    <section class="person">
      <h1 class="person-name">Kelvan Joshi</h1>
      <p class="person-title">Designated Partner</p>
      <ul class="contact-list">
        <li>
          <svg viewBox="0 0 24 24" aria-hidden="true"><path d="M6.6 10.8a15 15 0 0 0 6.6 6.6l2.2-2.2c.3-.3.7-.4 1-.2 1.1.4 2.3.6 3.6.6.6 0 1 .4 1 1V20c0 .6-.4 1-1 1A17 17 0 0 1 3 4c0-.6.4-1 1-1h3.5c.6 0 1 .4 1 1 0 1.3.2 2.5.6 3.6.1.3 0 .7-.2 1z"/></svg>
          +91 97415 60382
        </li>
        <li>
          <svg viewBox="0 0 24 24" aria-hidden="true"><path d="M2 5h20v14H2zm2 2v.5l8 5 8-5V7zm0 2.8V17h16V9.8l-8 5z"/></svg>
          kelvanjoshi@mailbrook.example
        </li>
        <li>
          <svg viewBox="0 0 24 24" aria-hidden="true"><circle cx="12" cy="12" r="10"/></svg>
          www.greymarshcontracts.example
        </li>
      </ul>
    </section>

    <address class="address">
      Greymarsh Engineering Contracts LLP<br>
      Block No.317, Wing C, Tulvo Trade Court,<br>
      Manek Pural Road, Ruparel Industrial Estate, Goregaon(E), Mumbai - 400 063
    </address>
  </article>
</main>
</body>
</html>
```